Communication and Marketing agency needs a new presentation card

We are a group of communication and marketing agencies specialized in companies that are in the logistics and industrial sector. The head agency is TELVANO Grupo and the group consists of 4 agencies: TELVANO Media, TELVANO Digital, TELVANO Research and DifundeEnPantalla. We hace 4 offices in Spain (Madrid, Barcelona, Valencia and Murcia). We are looking for a clean and attractive design that transmits our experience, brand presence in the market and knowledge to those who receive the card.It has to maintain the colors of the logo that is attached.
Target Market(s)
logistics and industrial sector
Marketing department
Contact Information for Business Card
Clean and attractive design

```html
<!DOCTYPE html>
<html lang="es">
<head>
<meta charset="utf-8">
<title>TELVANO Grupo – Tarjeta de presentación</title>
<link rel="stylesheet" href="https://fonts.googleapis.com/css2?family=Open+Sans:wght@400;600;700&display=swap">
<style>
  :root {
    --bg: #262628;
    --card: #1b1b1c;
    --red: #c8202f;
    --white: #f2f2f2;
    --grey: #8a8a8c;
    --muted: #d8d8d8;
  }
  * { box-sizing: border-box; margin: 0; padding: 0; }
  html, body { width: 1200px; height: 900px; overflow: hidden; }
  body {
    background: var(--bg);
    font-family: "Open Sans", sans-serif;
    position: relative;
  }
  .card {
    position: absolute;
    left: 320px;
    width: 560px;
    height: 320px;
    background: var(--card);
    border-radius: 22px;
    box-shadow: 0 10px 30px rgba(0,0,0,.45);
  }
  .card--front { top: 85px; }
  .card--back { top: 495px; }

  .brand {
    font-family: "Open Sans", sans-serif;
    font-weight: 400;
    letter-spacing: 2px;
    white-space: nowrap;
    position: absolute;
  }
  .card--front .brand {
    color: var(--white);
    font-size: 44px;
    left: 170px;
    top: 95px;
  }
  .offices {
    position: absolute;
    right: 48px;
    bottom: 42px;
    color: var(--muted);
    font-size: 12.5px;
    letter-spacing: .3px;
  }

  .card--back .brand--main {
    color: var(--red);
    font-size: 44px;
    right: 40px;
    top: 38px;
  }
  .contact {
    position: absolute;
    left: 40px;
    bottom: 36px;
    color: var(--white);
  }
  .contact__name {
    color: var(--red);
    font-weight: 700;
    font-size: 19px;
    letter-spacing: .5px;
  }
  .contact__role {
    font-size: 15px;
    margin-bottom: 8px;
  }
  .contact__list { list-style: none; }
  .contact__item {
    display: flex;
    align-items: center;
    gap: 8px;
    font-size: 16px;
    line-height: 22px;
  }
  .contact__item svg { width: 13px; height: 13px; fill: var(--red); flex: none; }

  .agencies {
    position: absolute;
    right: 36px;
    bottom: 52px;
    display: grid;
    grid-template-columns: auto auto;
    column-gap: 18px;
    row-gap: 22px;
    justify-items: end;
  }
  .agency {
    font-size: 14px;
    font-weight: 400;
    letter-spacing: .5px;
    white-space: nowrap;
  }
  .agency--grey { color: var(--grey); }
  .agency--red { color: var(--red); }
</style>
</head>
<body>

  <section class="card card--front" aria-label="Anverso de la tarjeta">
    <div class="brand">TELVANO Grupo</div>
    <p class="offices">MADRID, BARCELONA, VALENCIA, MURCIA</p>
  </section>

  <section class="card card--back" aria-label="Reverso de la tarjeta">
    <div class="brand brand--main">TELVANO Grupo</div>

    <div class="contact">
      <p class="contact__name">MARCOS FERRER</p>
      <p class="contact__role">Managing Director</p>
      <ul class="contact__list">
        <li class="contact__item">
          <svg viewBox="0 0 16 16" aria-hidden="true"><path d="M3 1h3l1.5 4-2 1.3a9 9 0 0 0 4.2 4.2L11 8.5l4 1.5v3a2 2 0 0 1-2 2A13 13 0 0 1 1 3a2 2 0 0 1 2-2z"/></svg>
          044-318 672 540
        </li>
        <li class="contact__item">
          <svg viewBox="0 0 16 16" aria-hidden="true"><path d="M4 0h8a1 1 0 0 1 1 1v14a1 1 0 0 1-1 1H4a1 1 0 0 1-1-1V1a1 1 0 0 1 1-1zm1 2v10h6V2zm3 11a1 1 0 1 0 0 2 1 1 0 0 0 0-2z"/></svg>
          044-318 672 541
        </li>
        <li class="contact__item">
          <svg viewBox="0 0 16 16" aria-hidden="true"><path d="M1 3h14v10H1zm1.5 1.2L8 8.5l5.5-4.3z"/></svg>
          info@telvanogrupo.es
        </li>
        <li class="contact__item">
          <svg viewBox="0 0 16 16" aria-hidden="true"><circle cx="8" cy="8" r="7"/></svg>
          www.telvanogrupo.es
        </li>
      </ul>
    </div>

    <div class="agencies">
      <span class="agency agency--grey">TELVANO Research</span>
      <span class="agency agency--grey">TELVANO Digital</span>
      <span class="agency agency--red">TELVANO Media</span>
      <span class="agency agency--red">DifundeEnPantalla</span>
    </div>
  </section>

</body>
</html>
```